KVM Contracting services . Building and maintenance services, optic fibre installation

Business cards and logo design.I need a logo that I can use on business cards ,workwear and on my vehicles. I would like the KVM to be the main or larger text and contracting services to be the smaller or less important text.I like monograms, modern designs and repeating patterns symbols. I am also a Gemini and my favourite number is 22 so if this can be any inspiration to help with the design. Am thinking of the using German flag colours as a his is my family’s heritage. And the other 2 main colours I wear is black and white.But any ideas are appreciated.I do not need a design that is trade specific but a design that could be used for any business.

Target Market(s)

General public

Contact Information for Business Card

KVM Contracting Services ( front of business card)

(Back of business card)
Darren Holtwick
0451907326
Maintenance services
Optic fibre and data installation

Logo Text

Logo can just be pattern or monogram or incorporate KVM . I like the gemini star sign and the number 22

Colors
ec1f27
000000
fbee3e
ffffff

Requirements
Must have
• Logo and KVM Contracting Services on the front of business card
Nice to have
• Possible use of German flag colours.
• Modern design.
• Design to be able to be used on black or white background as I want to put it on clothing

```html
<!DOCTYPE html>
<html lang="en">
<head>
<meta charset="utf-8">
<title>KVM Contracting Services – Business Cards</title>
<link href="https://fonts.googleapis.com/css2?family=Lato:wght@400;700;900&display=swap" rel="stylesheet">
<style>
  :root {
    --backdrop: #2a2a2a;
    --card: #1c1c1c;
    --card-edge: #262626;
    --red: #ec1f27;
    --yellow: #fbee3e;
    --white: #ffffff;
    --grey: #8a8a8a;
  }
  * { margin: 0; padding: 0; box-sizing: border-box; }
  html, body {
    width: 1200px; height: 900px; overflow: hidden;
    background: var(--backdrop);
    font-family: "Lato", Arial, sans-serif;
  }
  .sheet {
    width: 1200px; height: 900px;
    display: flex; flex-direction: column; align-items: center; justify-content: center;
    gap: 40px;
  }
  .card {
    width: 620px; height: 354px;
    background: linear-gradient(135deg, var(--card) 0%, var(--card-edge) 100%);
    box-shadow: 0 14px 30px rgba(0,0,0,.45);
    position: relative;
  }
  /* front */
  .card--front {
    display: flex; flex-direction: column; align-items: center; justify-content: center;
  }
  .brand-name {
    font-weight: 900; text-transform: uppercase; line-height: 1;
    display: flex; align-items: center; gap: 14px;
  }
  .brand-mark { width: 18px; height: 18px; flex: none; }
  .card--front .brand-name { color: var(--grey); font-size: 30px; }
  .card--front .brand-mark { background: var(--grey); }
  .front-services {
    margin-top: 34px; text-align: center; text-transform: uppercase;
    letter-spacing: 1.5px; font-size: 14px; line-height: 1.45;
  }
  .front-services .service-main { color: var(--yellow); }
  .front-services .service-sub { color: var(--white); }
  /* back */
  .card--back {
    display: flex; align-items: center; padding: 0 40px 0 48px;
  }
  .back-brand { width: 250px; }
  .card--back .brand-name { color: var(--red); font-size: 23px; flex-wrap: nowrap; }
  .card--back .brand-mark { background: var(--red); width: 14px; height: 14px; }
  .divider {
    width: 2px; height: 150px; background: var(--white); margin: 0 30px 0 14px; flex: none;
  }
  .contact { color: var(--white); font-size: 15.5px; line-height: 1.3; }
  .person-name { color: var(--red); font-size: 24px; font-weight: 400; letter-spacing: .5px; text-transform: uppercase; }
  .person-role { font-size: 16px; margin-bottom: 16px; }
  .address { margin-bottom: 8px; }
  .contact-line { display: flex; align-items: center; gap: 10px; }
  .contact-line svg { width: 11px; height: 11px; flex: none; }
</style>
</head>
<body>
<main class="sheet">
  <section class="card card--front" aria-label="Business card front">
    <div class="brand-name"><span class="brand-mark"></span>KVM Contracting Services</div>
    <div class="front-services">
      <div class="service-main">Maintenance Services</div>
      <div class="service-sub">Optic Fibre and Data Installation</div>
    </div>
  </section>

  <section class="card card--back" aria-label="Business card back">
    <div class="back-brand">
      <div class="brand-name"><span class="brand-mark"></span>KVM Contracting Services</div>
    </div>
    <div class="divider"></div>
    <div class="contact">
      <div class="person-name">Darren Holtwick</div>
      <div class="person-role">Director</div>
      <div class="address">18 Larkmoor Rd,<br>Fenwick Bay, FL 32190, USA</div>
      <div class="contact-line">
        <svg viewBox="0 0 12 12"><path d="M2 1h2.5l1 3-1.5 1a7 7 0 0 0 3 3l1-1.5 3 1V10a1 1 0 0 1-1 1A9 9 0 0 1 1 2a1 1 0 0 1 1-1z" fill="var(--red)"/></svg>
        <span>0451907326</span>
      </div>
      <div class="contact-line">
        <svg viewBox="0 0 12 12"><rect x="1" y="2.5" width="10" height="7" fill="none" stroke="var(--red)" stroke-width="1.2"/><path d="M1 2.5l5 4 5-4" fill="none" stroke="var(--red)" stroke-width="1.2"/></svg>
        <span>office@kvmbuildco.com</span>
      </div>
      <div class="contact-line">
        <svg viewBox="0 0 12 12"><circle cx="6" cy="6" r="5" fill="none" stroke="var(--red)" stroke-width="1.1"/><ellipse cx="6" cy="6" rx="2.2" ry="5" fill="none" stroke="var(--red)" stroke-width="1"/><path d="M1 6h10" stroke="var(--red)" stroke-width="1"/></svg>
        <span>www.kvmbuildco.com</span>
      </div>
    </div>
  </section>
</main>
</body>
</html>
```